Yoga Workshop - Yoga Practice information flyer

I am a yoga teacher who will be presenting a workshop on yoga for sleep and need a brochure for my clients which outlines a practice that I give them so they can do the practice at home. Ideally I would like a brochure that is a single A3 size of paper in size that folds in half to an A4 booklet with the entire practice on the centre section to make it easy for people to do the practice at home with just one open page in front of them:
* Front page detailing "Yoga for Sleep Workshop" and "Restorative Yoga Practice"
* Centre contains the information on the practice contained in the attached word document. The practice consists of 5 postures, so there needs to be five separate sections which have the pictures of the postures (attached in uploaded files) and the wording contained in the attached word document. All pictures uploaded need to be included in the flyer as each posture has different pictures demonstrating the posture using yoga props or using things people have at home
* Back page containing a picture of myself (picture uploaded in files) with some information about me (contained in the attached word document) and my website www.calmdrift.com.au

I also need this flyer to be able to printed on 2 double sided A4 sheets of paper so will require 2 x pdf file versions. Importantly, for the centre section of the flyer, the design needs to ensure if it is printed on A4 paper, the wording and pictures for each of the postures are not separated over two pages

Target Market(s)

Existing clients

Requirements
Must have
• Detailed in project description
Nice to have
• The word document also contains some quotes. These do not need to be included in the flyer. If there is room and there is room for one or two of those please include where it would look good
Should not have
• Stock pictures of people in yoga postures which a normal everyday person could not get into

```html
<!DOCTYPE html>
<html lang="en">
<head>
<meta charset="utf-8">
<title>Restorative Yoga Practice – Postures 1 &amp; 2</title>
<link href="https://fonts.googleapis.com/css2?family=Josefin+Sans:ital,wght@0,400;0,600;1,600&display=swap" rel="stylesheet">
<style>
  :root {
    --navy: #34475e;
    --peach: #e6a47f;
    --copper: #c98a6a;
    --white: #ffffff;
    --ink: #34475e;
    --photo-warm: #8a5a3c;
    --photo-cool: #3f7f9c;
  }
  * { margin: 0; padding: 0; box-sizing: border-box; }
  html, body { width: 848px; height: 1200px; overflow: hidden; background: var(--white); }
  .page {
    position: relative;
    width: 848px;
    height: 1200px;
    overflow: hidden;
    font-family: "Josefin Sans", sans-serif;
    background: var(--white);
  }
  .backdrop { position: absolute; inset: 0; width: 848px; height: 1200px; }
  .photo-frame { position: absolute; padding: 5px; }
  .photo-frame.white { background: var(--white); }
  .photo-frame.copper { background: var(--copper); }
  .photo-frame.navy { background: var(--navy); }
  .photo {
    width: 100%;
    height: 100%;
    background: linear-gradient(160deg, var(--photo-warm) 0%, var(--photo-cool) 100%);
  }
  .posture {
    position: absolute;
    left: 35px;
    width: 764px;
  }
  .posture-title {
    font-weight: 600;
    font-size: 20px;
    line-height: 22px;
    letter-spacing: 0.3px;
    color: var(--peach);
    margin-bottom: 12px;
  }
  .posture p {
    font-size: 14.9px;
    line-height: 15.7px;
    letter-spacing: 0.4px;
    margin-bottom: 15.7px;
    hyphens: auto;
    -webkit-hyphens: auto;
  }
  .posture .label {
    font-style: italic;
    font-weight: 600;
    color: var(--peach);
  }
  .posture.on-navy p { color: var(--white); }
  .posture.on-white p { color: var(--ink); }
</style>
</head>
<body>
<div class="page">
  <svg class="backdrop" viewBox="0 0 848 1200" aria-hidden="true">
    <path d="M0 0 H848 V674 Q424 590 0 674 Z" fill="var(--navy)"/>
  </svg>

  <div class="photo-frame white" style="left:34px;top:39px;width:232px;height:312px;">
    <div class="photo" role="img" aria-label="Woman lying on a yoga mat with a bolster under her knees and a cushion under her head"></div>
  </div>
  <div class="photo-frame copper" style="left:302px;top:39px;width:232px;height:312px;">
    <div class="photo" role="img" aria-label="Woman lying on a yoga mat with a rolled towel under her knees"></div>
  </div>
  <div class="photo-frame white" style="left:570px;top:39px;width:232px;height:312px;">
    <div class="photo" role="img" aria-label="Woman sitting at the end of a lengthways rolled towel before lying back"></div>
  </div>

  <section class="posture on-navy" style="top:380px;">
    <h2 class="posture-title">Posture 1 – Supported Chest Opening with Knee Support</h2>
    <p><span class="label">Props</span> – 2 x bolsters (or towels rolled up lengthways), 1 x cushion for head support (optional)</p>
    <p><span class="label">Set up notes</span> – Position the props in a T-position with one bolster/towel running parallel to the yoga mat and one bolster or towel running horizontal to the mat underneath the knees. The hips will be on the ground and the parallel support bolster/towel will rest along the spine starting from a comfortable place at the base of the rib cage to behind the head</p>
    <p><span class="label">Caution</span> – If any lower back pain is experience adjust the parallel bolster height by using a towel rolled up lengthways. The length of the towel may be extended so the entire spine from sacrum (flat bony structure at the base of the spine) to the back of the head is lying on the towel of folded blanket. Do not use any parallel support prop if pain continues.</p>
  </section>

  <div class="photo-frame copper" style="left:171px;top:624px;width:232px;height:298px;">
    <div class="photo" role="img" aria-label="Woman in supported bound-angle pose with yoga blocks under her knees"></div>
  </div>
  <div class="photo-frame navy" style="left:439px;top:630px;width:232px;height:292px;">
    <div class="photo" role="img" aria-label="Woman in supported bound-angle pose with pillows under her knees"></div>
  </div>

  <section class="posture on-white" style="top:952px;">
    <h2 class="posture-title">Posture 2 – Supported Bound-Angle Pose</h2>
    <p><span class="label">Props</span> – 1 x bolsters (or towel rolled up lengthways), 2 x yoga blocks/bolsters (or pillows), 1 x cushion for head support (optional)</p>
    <p><span class="label">Set up notes</span> – Similar to Posture 1 without the bolster behind the knees. Instead, the soles of the feet are together with knees wide being supported by either blocks, bolsters or pillows. The support under the knees can be as high as needed to rest comfortably in the posture.</p>
    <p><span class="label">Caution</span> – If any lower back pain is experience adjust the parallel bolster height by using a towel rolled up lengthways. The length of the towel may be extended so the entire spine from sacrum (flat bony structure at the base of the spine) to the back of the head is lying on the towel of folded blanket. Do not use any parallel support prop if pain continues.</p>
  </section>
</div>
</body>
</html>
```